Corvy

Electronic Repairs for OEM's Industrial electronic repairs, consumer audio visual, Projectors

Target Market(s)

manufacturer of electronics (OEM), business, Government, then Consumer

Industry/Entity Type

Electronic Repair

Contact Information for Business Card

Board Repair, Projectors

Font styles to use
Serif

Colors
0054AA
0677BA
7BADD7
CADEEF
E8F1F8

Requirements
Must have
• projector, led wall image
Nice to have
• professional looking business card.
Should not have
• unsure

```html
<!DOCTYPE html>
<html lang="en">
<head>
<meta charset="utf-8">
<title>Corvy Electronic Repairs – Business Card</title>
<link rel="stylesheet" href="https://fonts.googleapis.com/css2?family=Montserrat:wght@400;800&family=Noto+Sans:wght@400;700&display=swap">
<style>
  :root {
    --brand-blue: #0054AA;
    --mid-blue: #0677BA;
    --soft-blue: #7BADD7;
    --pale-blue: #CADEEF;
    --mist-blue: #E8F1F8;
    --card-face: #ECEDEF;
    --ink: #141821;
    --page: #DDE2E8;
  }
  * { margin: 0; padding: 0; box-sizing: border-box; }
  html, body {
    width: 1200px;
    height: 840px;
    overflow: hidden;
    background: var(--page);
  }
  .canvas {
    position: relative;
    width: 1200px;
    height: 840px;
  }
  .card {
    position: absolute;
    left: 75px;
    top: 120px;
    width: 1050px;
    height: 600px;
    border-radius: 34px;
    background: var(--card-face);
    overflow: hidden;
    box-shadow: 0 18px 40px rgba(20, 40, 70, 0.18);
  }
  .card-art {
    position: absolute;
    inset: 0;
  }
  .brand {
    position: absolute;
    left: 100px;
    top: 62px;
    color: var(--brand-blue);
  }
  .brand-name {
    font-family: "Montserrat", sans-serif;
    font-weight: 800;
    font-size: 116px;
    line-height: 1;
    letter-spacing: -2px;
    text-transform: uppercase;
  }
  .brand-tagline {
    font-family: "Montserrat", sans-serif;
    font-weight: 400;
    font-size: 38px;
    line-height: 1;
    margin-top: 8px;
    color: var(--mid-blue);
    letter-spacing: 0.5px;
  }
  .service-summary {
    position: absolute;
    left: 100px;
    top: 262px;
    font-family: "Noto Sans", sans-serif;
    font-weight: 700;
    font-size: 22px;
    line-height: 29px;
    color: var(--brand-blue);
  }
  .summary-line { display: block; white-space: nowrap; }
  .service-list {
    position: absolute;
    left: 100px;
    top: 374px;
    list-style: none;
    font-family: "Noto Sans", sans-serif;
    font-size: 26px;
    color: var(--ink);
  }
  .service-item {
    display: flex;
    align-items: center;
    gap: 16px;
    height: 40px;
  }
  .tick-icon { width: 28px; height: 28px; flex: none; }
  .call-line {
    position: absolute;
    left: 100px;
    top: 506px;
    display: flex;
    align-items: baseline;
    gap: 16px;
    font-family: "Montserrat", sans-serif;
    font-weight: 800;
    line-height: 1;
  }
  .call-label {
    font-size: 38px;
    color: var(--brand-blue);
  }
  .call-number {
    font-size: 44px;
    color: var(--ink);
  }
</style>
</head>
<body>
<main class="canvas">
  <section class="card" aria-label="Corvy Electronic Repairs business card">
    <svg class="card-art" viewBox="0 0 1050 600" width="1050" height="600">
      <defs>
        <radialGradient id="projector-tones" cx="50%" cy="55%" r="60%">
          <stop offset="0" stop-color="#7BADD7"/>
          <stop offset="0.55" stop-color="#1F5C86"/>
          <stop offset="1" stop-color="#0B2E4A"/>
        </radialGradient>
        <linearGradient id="ledwall-tones" x1="0" y1="0" x2="0" y2="1">
          <stop offset="0" stop-color="#E3E6EA"/>
          <stop offset="1" stop-color="#C9CDD3"/>
        </linearGradient>
        <radialGradient id="board-tones" cx="50%" cy="50%" r="60%">
          <stop offset="0" stop-color="#7BADD7"/>
          <stop offset="0.6" stop-color="#1D5FA0"/>
          <stop offset="1" stop-color="#0A3565"/>
        </radialGradient>
      </defs>
      <path class="accent-band-edge" d="M730,0 C930,120 930,470 860,600 L1050,600 L1050,0 Z" fill="var(--mid-blue)"/>
      <path class="accent-band" d="M754,0 C952,126 952,470 884,600 L1050,600 L1050,0 Z" fill="var(--brand-blue)"/>

      <circle class="photo-projector" cx="748" cy="172" r="90" fill="url(#projector-tones)" stroke="#E6E8EB" stroke-width="6"
              role="img" aria-label="Photo of a ceiling-mounted video projector with its lamp lit"/>
      <circle class="photo-ledwall" cx="912" cy="292" r="98" fill="url(#ledwall-tones)" stroke="#E6E8EB" stroke-width="6"
              role="img" aria-label="Image of an LED wall panel frame"/>
      <circle class="photo-board" cx="808" cy="452" r="94" fill="url(#board-tones)" stroke="#E6E8EB" stroke-width="6"
              role="img" aria-label="Close-up photo of a blue circuit board being repaired"/>
    </svg>

    <header class="brand">
      <h1 class="brand-name">Corvy</h1>
      <p class="brand-tagline">ELECTRONIC REPAIRS</p>
    </header>

    <p class="service-summary">
      <span class="summary-line">Electronic Repairs for</span>
      <span class="summary-line">OEM's Industrial electronic repairs,</span>
      <span class="summary-line">consumer audio visual, Projectors</span>
    </p>

    <ul class="service-list">
      <li class="service-item">
        <svg class="tick-icon" viewBox="0 0 28 28" aria-hidden="true"><circle cx="14" cy="14" r="14" fill="var(--brand-blue)"/><path d="M8 14.5l4 4 8-9" fill="none" stroke="#fff" stroke-width="3" stroke-linecap="round" stroke-linejoin="round"/></svg>
        Projector
      </li>
      <li class="service-item">
        <svg class="tick-icon" viewBox="0 0 28 28" aria-hidden="true"><circle cx="14" cy="14" r="14" fill="var(--brand-blue)"/><path d="M8 14.5l4 4 8-9" fill="none" stroke="#fff" stroke-width="3" stroke-linecap="round" stroke-linejoin="round"/></svg>
        Led wall image
      </li>
      <li class="service-item">
        <svg class="tick-icon" viewBox="0 0 28 28" aria-hidden="true"><circle cx="14" cy="14" r="14" fill="var(--brand-blue)"/><path d="M8 14.5l4 4 8-9" fill="none" stroke="#fff" stroke-width="3" stroke-linecap="round" stroke-linejoin="round"/></svg>
        Board Repair
      </li>
    </ul>

    <p class="call-line">
      <span class="call-label">CALL US</span>
      <span class="call-number">555-014-2387</span>
    </p>
  </section>
</main>
</body>
</html>
```